professional business card design for technology company

We are a small technology consulting firm, specialising in consulting based around Cloud and Managed services. Our colour scheme is yellow, blue and white, as you can see in the logos. Although we are based in melbourne australia, due to the nature of our work, our clients can be located anywhere. We are looking for a clean, professional, positive look - similar to our company logo

Target Market(s)

small business

Industry/Entity Type

Business

Contact Information for Business Card

eye catching, designed to incorporate some level of raised printing. Must contain website address, phone number, name and job title

Requirements
Must have
• Logo (attached) - use of the same colour scheme

```html
<!DOCTYPE html>
<html lang="en">
<head>
<meta charset="utf-8">
<title>Skyvane business card</title>
<link rel="stylesheet" href="https://fonts.googleapis.com/css2?family=Lato:wght@400;700;900&display=swap">
<style>
  :root {
    --backdrop: #2b2b2b;
    --card: #f7f7f7;
    --ink: #1c1c1c;
    --brand-grey: #4a4a4a;
    --blue: #3a9bd8;
    --blue-deep: #2c86c4;
    --yellow: #f1d23a;
  }
  * { box-sizing: border-box; margin: 0; padding: 0; }
  html, body { width: 1200px; height: 873px; overflow: hidden; }
  body {
    background: var(--backdrop);
    font-family: "Lato", Arial, sans-serif;
    position: relative;
  }
  .card {
    position: absolute;
    width: 520px;
    height: 297px;
    background: var(--card);
    overflow: hidden;
  }
  .card--front { left: 60px; top: 150px; }
  .card--back { left: 620px; top: 426px; }
  .card__band { position: absolute; left: 0; bottom: 0; width: 520px; height: 24px; }

  .brand { display: flex; align-items: center; gap: 14px; }
  .brand__dot { width: 40px; height: 40px; border-radius: 50%; background: var(--blue); }
  .brand__name { font-weight: 900; color: var(--brand-grey); letter-spacing: -1px; }

  .card--front .brand { position: absolute; left: 0; right: 0; top: 112px; justify-content: center; }
  .card--front .brand__name { font-size: 58px; }

  .back__left { position: absolute; left: 0; top: 0; width: 260px; height: 100%; }
  .card--back .brand { position: absolute; left: 44px; top: 82px; gap: 10px; }
  .card--back .brand__dot { width: 30px; height: 30px; }
  .card--back .brand__name { font-size: 38px; }
  .back__web { position: absolute; left: 0; width: 260px; top: 178px; text-align: center; font-size: 13px; font-weight: 700; color: var(--brand-grey); }
  .back__web span { color: var(--blue); }
  .back__address { position: absolute; left: 0; width: 260px; top: 212px; text-align: center; font-size: 14px; font-weight: 700; color: var(--blue); line-height: 1.35; }

  .back__divider { position: absolute; left: 264px; top: 30px; width: 2px; height: 200px;
    background: linear-gradient(to bottom, rgba(58,155,216,0), var(--blue) 30%, var(--blue) 60%, rgba(58,155,216,0)); }

  .person { position: absolute; left: 290px; top: 44px; }
  .person__name { font-size: 17px; font-weight: 900; color: var(--blue); }
  .person__title { font-size: 11px; font-weight: 700; color: var(--ink); margin-top: 2px; }

  .contacts { position: absolute; left: 290px; top: 130px; list-style: none; }
  .contacts li { display: flex; align-items: center; gap: 8px; height: 24px; font-size: 14px; font-weight: 700; color: var(--ink); }
  .contacts svg { width: 18px; height: 18px; flex: none; }
</style>
</head>
<body>

<section class="card card--front" aria-label="Card front">
  <div class="brand">
    <span class="brand__dot"></span>
    <span class="brand__name">Skyvane</span>
  </div>
  <svg class="card__band" viewBox="0 0 520 24" preserveAspectRatio="none">
    <path d="M300 24 C306 12 312 10 330 10 L520 10 L520 24 Z" fill="var(--blue)"/>
  </svg>
</section>

<section class="card card--back" aria-label="Card back">
  <div class="back__left">
    <div class="brand">
      <span class="brand__dot"></span>
      <span class="brand__name">Skyvane</span>
    </div>
    <p class="back__web">www.<span>skyvane</span>.com</p>
    <p class="back__address">2280 Harbor Lane #210<br>Ocean Ridge, Florida 33401</p>
  </div>

  <div class="back__divider"></div>

  <div class="person">
    <p class="person__name">Daniel R. Hartley</p>
    <p class="person__title">Broker / Owner</p>
  </div>

  <ul class="contacts">
    <li>
      <svg viewBox="0 0 18 18"><circle cx="9" cy="9" r="9" fill="var(--blue)"/><path d="M5 7 Q9 4 13 7 L12 8.5 L10.5 7.5 L7.5 7.5 L6 8.5 Z M6 9.5 L12 9.5 L12.5 13 L5.5 13 Z" fill="#fff"/></svg>
      555-204-3181
    </li>
    <li>
      <svg viewBox="0 0 18 18"><circle cx="9" cy="9" r="9" fill="var(--blue)"/><rect x="6" y="4" width="6" height="10" rx="1" fill="#fff"/><rect x="7" y="5.5" width="4" height="6" fill="var(--blue)"/></svg>
      555-318-6420
    </li>
    <li>
      <svg viewBox="0 0 18 18"><circle cx="9" cy="9" r="9" fill="var(--blue)"/><rect x="6.5" y="4" width="5" height="4" fill="#fff"/><rect x="4.5" y="8" width="9" height="5" rx="1" fill="#fff"/></svg>
      555-472-9035
    </li>
    <li>
      <svg viewBox="0 0 18 18"><circle cx="9" cy="9" r="9" fill="var(--blue)"/><rect x="4.5" y="5.5" width="9" height="7" fill="#fff"/><path d="M4.5 5.5 L9 9.5 L13.5 5.5" fill="none" stroke="var(--blue)" stroke-width="1"/></svg>
      dan.hartley@mailbox.com
    </li>
  </ul>

  <svg class="card__band" viewBox="0 0 520 24" preserveAspectRatio="none">
    <path d="M280 24 C286 12 292 10 310 10 L520 10 L520 24 Z" fill="var(--blue)"/>
  </svg>
</section>

</body>
</html>
```